July 2022 Industrial Manufacturer Product Expo Mexico City

We manufacture large screws and fastners for large Mining equipment, Trains, large ships, airplanes, wind turbines, and so on. We also do custom work base on the customer needs. No matter the size we can make it.
We have a Expo coming up with companies all over the world. We have to stand out we are a family own business so our customer service will be above and beyond anyone can provide. We do not have a sales force to push our products and services we provide one on one service.
Plus@!! I'm looking for anything that you designers can come up with if it was your company to put on a business card, plus i want to do a 1 or 2 sided pamphlet, and then a website. We make Speciality Bolts for large mining equipment these bolts can be 3 to 4 foot long!!! Plus fasteners, Nuts, washers, any, size, strengths, special materials, we offer more of a ono on one customer service, We are a small company, family own, but can fulfill any type of orders. We can also provide special time lines for emergency orders. "We keep the machines running we here at KRV don't believe in down time" We want to hear any slogan based on our company to stand out.
Thanks i really appreciate all your work and options that we have to pick on. Plus just a thought we could possibly want to entertain a experience Marketing internet help maybe a employment possibility. Thanks

I need 2 cards one in Spanish and English Like the steel back ground maybe send me in some bright red and blue writing Same with the Black cards Please remove the word Military The logo KRV maybe integrate a picture of a Bolt 🔩 Thank you

Still looking for I need 2 cards one in Spanish and English Like the steel back ground maybe send me in some bright red and blue writing Same with the Black cards try bright writing Please remove the word Military The logo KRV maybe integrate a picture of a Bolt 🔩 Plus will need the company to make a brochure and website next Thank you

Target Market(s)

Large Mining, Ship, Train, Green Energy, VELM, and Government equipment. Throughout the World

Industry/Entity Type

We can Custom Manufacture any type of Fastners for Mining equipment, Trains, Ships, Green energy, Governments, or military projects. wind turbines,

Contact Information for Business Card

I attached the name and contact info that's on a card, plus the Company Logo. Would like industrial looking background with Bright Colors that will stand out!! If we can insert somewhere maybe on back that we "Custom Manufacture Any Size or Quantity Fastners for Large Mining Equipment, Trains, Ships, Green Energy Equipment or Government Projects

Font styles to use
Other font styles liked:
• You Pick, has to be bold, colorful standout, Professional looking Beable to read it.

Colors

Designer to choose colors to be used in the design.

Requirements
Must have
• Need in Spanish and English TO STANDOUT FROM THE REST OF THE EXPO!! See Business card details, Rounded corners
Nice to have
• Can i see some of the darker cards with Bright Red and Blue letters I like to see the different type of card material, heavy thickness, plastic, transparent, Metal types, Bright Colors, I saw like Raised letters like on the logo.

```html
<!DOCTYPE html>
<html lang="es">
<head>
<meta charset="utf-8">
<title>KRV – Business Cards</title>
<link rel="stylesheet" href="https://fonts.googleapis.com/css2?family=Cinzel:wght@400;700&family=Open+Sans:wght@400;600;700&display=swap">
<style>
  :root{
    --backdrop:#c9c9c9;
    --card-dark-top:#6b6b70;
    --card-dark-bottom:#030303;
    --silver:#d4d4d8;
    --white:#ffffff;
    --blue-bright:#1a8ad4;
    --blue-navy:#1d3f96;
    --logo-blue:#0b5fb0;
    --ghost:#ececf1;
  }
  *{margin:0;padding:0;box-sizing:border-box}
  html,body{width:1200px;height:900px;overflow:hidden;background:var(--backdrop)}
  .canvas{position:relative;width:1200px;height:900px}
  .card{position:absolute;width:560px;height:320px;border-radius:30px;overflow:hidden}

  /* back side */
  .card--back{left:320px;top:100px;background:linear-gradient(180deg,var(--card-dark-top) 0%,#1a1a1c 55%,var(--card-dark-bottom) 100%)}
  .card--back .brand{position:absolute;left:0;right:0;top:62px;text-align:center;font-family:'Cinzel',serif;font-weight:700;font-size:88px;letter-spacing:10px;color:var(--silver);line-height:1}
  .card--back .tagline{position:absolute;left:40px;right:40px;top:186px;text-align:center;font-family:'Cinzel',serif;font-weight:400;font-size:15px;line-height:1.35;color:var(--white);letter-spacing:.3px}

  /* front side */
  .card--front{left:320px;top:480px;background:var(--white)}
  .card--front .brand{position:absolute;left:46px;top:30px;font-family:'Open Sans',sans-serif;font-weight:700;font-size:80px;letter-spacing:6px;color:var(--logo-blue);line-height:1}
  .card--front .brand-ghost{position:absolute;right:30px;top:92px;font-family:'Open Sans',sans-serif;font-weight:700;font-size:130px;letter-spacing:8px;color:var(--ghost);line-height:1}
  .contact{position:absolute;left:46px;top:142px;font-family:'Open Sans',sans-serif}
  .contact .name{font-weight:700;font-size:25px;color:var(--blue-bright);margin-bottom:10px}
  .contact .line{font-size:16px;color:var(--blue-navy);line-height:1.35}
  .contact .phone{display:flex;align-items:center;gap:8px;font-size:17px;color:var(--blue-navy);line-height:1.4}
  .contact .phone svg{width:16px;height:16px;flex:none}
</style>
</head>
<body>
<main class="canvas">

  <section class="card card--back" aria-label="Reverso de la tarjeta">
    <div class="brand">KRV</div>
    <p class="tagline">Custom Manufacture Any Size or Quantity<br>Fastners for Large Mining Equipment, Trains,<br>Ships, Green Energy Equipment,<br>Military or Government Projects</p>
  </section>

  <section class="card card--front" aria-label="Frente de la tarjeta">
    <div class="brand-ghost" aria-hidden="true">KRV</div>
    <div class="brand">KRV</div>
    <div class="contact">
      <p class="name">Lic.Marisol Ortega Vidal</p>
      <p class="line">Cotizaciones en</p>
      <p class="line">ventas.krv@correo-ejemplo.com</p>
      <p class="phone" style="margin-top:6px">
        <svg viewBox="0 0 24 24" aria-hidden="true"><path fill="#1d3f96" d="M6.6 10.8a15.2 15.2 0 0 0 6.6 6.6l2.2-2.2a1 1 0 0 1 1-.25 11.4 11.4 0 0 0 3.6.57 1 1 0 0 1 1 1V20a1 1 0 0 1-1 1A17 17 0 0 1 3 4a1 1 0 0 1 1-1h3.5a1 1 0 0 1 1 1c0 1.25.2 2.45.57 3.57a1 1 0 0 1-.25 1z"/></svg>
        5550123401
      </p>
      <p class="phone">
        <svg viewBox="0 0 24 24" aria-hidden="true"><rect x="6" y="2" width="12" height="20" rx="2" fill="none" stroke="#1d3f96" stroke-width="2"/><circle cx="12" cy="18" r="1.2" fill="#1d3f96"/></svg>
        5550187622
      </p>
    </div>
  </section>

</main>
</body>
</html>
```